brqnal new business card design project

we need a new business card design. you can view info about us @ brqnal-example.com. i have attached an example of our previous card with our previous name that we no longer use. We really liked the design, colors etc. look below to see more info about this project. it asks for a limited number of words. please see our website for more info about our compnay.

Target Market(s)

law enforcement

Contact Information for Business Card

i have uploaded an example of what we used before that we liked.

Font styles to use
Serif

```html
<!DOCTYPE html>
<html lang="en">
<head>
<meta charset="utf-8">
<title>BRQNAL Business Card</title>
<link rel="stylesheet" href="https://fonts.googleapis.com/css2?family=Lato:wght@300;400;700&family=Montserrat:wght@600&display=swap">
<style>
  :root {
    --backdrop: #7a7a7a;
    --card-light: #ffffff;
    --card-dark: #0c1a23;
    --ink: #0c1a23;
    --ink-soft: #555a5e;
    --rule: #a9adb0;
    --on-dark: #ffffff;
  }
  * { margin: 0; padding: 0; box-sizing: border-box; }
  html, body { width: 1200px; height: 1200px; overflow: hidden; }
  body {
    background: var(--backdrop);
    position: relative;
    font-family: "Lato", sans-serif;
  }
  .card {
    position: absolute;
    top: 310px;
    height: 594px;
    box-shadow: 3px 4px 8px rgba(0,0,0,0.35);
    text-align: center;
  }
  .card-front { left: 234px; width: 364px; background: var(--card-light); color: var(--ink); }
  .card-back { left: 627px; width: 370px; background: var(--card-dark); color: var(--on-dark); }

  .wordmark {
    position: absolute;
    left: 0; right: 0;
    font-family: "Lato", sans-serif;
    font-weight: 300;
    letter-spacing: 0.12em;
    line-height: 1;
  }
  .card-front .wordmark { top: 152px; font-size: 50px; color: var(--ink); }
  .card-back .wordmark { top: 240px; font-size: 56px; color: var(--on-dark); }

  .holder { position: absolute; top: 336px; left: 0; right: 0; }
  .holder-name {
    font-family: "Montserrat", sans-serif;
    font-weight: 600;
    font-size: 21px;
    letter-spacing: 0.03em;
    color: var(--ink);
  }
  .holder-title { font-size: 16px; color: var(--ink-soft); margin-top: 2px; }

  .icon-row {
    position: absolute;
    top: 396px; left: 88px;
    width: 188px; height: 22px;
  }
  .contact {
    position: absolute;
    top: 430px; left: 0; right: 0;
    font-size: 16px;
    line-height: 22px;
    color: var(--ink-soft);
  }
  .contact-rule {
    width: 170px; height: 1px;
    background: #dcdcdc;
    margin: 10px auto 10px;
  }

  .tagline {
    position: absolute;
    top: 308px; left: 0; right: 0;
    font-weight: 700;
    font-size: 16.5px;
    letter-spacing: 0.02em;
  }
  .divider {
    position: absolute;
    top: 449px; left: 76px;
    width: 217px; height: 1px;
    background: var(--on-dark);
    opacity: 0.8;
  }
  .services {
    position: absolute;
    top: 467px; left: 0; right: 0;
    list-style: none;
    font-size: 17px;
    line-height: 27px;
    letter-spacing: 0.02em;
  }
</style>
</head>
<body>
  <section class="card card-front">
    <div class="wordmark">BRQNAL</div>
    <div class="holder">
      <div class="holder-name">DANIEL BROOKS</div>
      <div class="holder-title">Managing Director</div>
    </div>
    <svg class="icon-row" viewBox="0 0 188 22" aria-hidden="true">
      <line x1="0" y1="11" x2="52" y2="11" stroke="var(--rule)" stroke-width="1.5"/>
      <line x1="136" y1="11" x2="188" y2="11" stroke="var(--rule)" stroke-width="1.5"/>
      <circle cx="66" cy="11" r="11" fill="var(--ink)"/>
      <path d="M61 15 q0-3 5-3 q5 0 5 3 z M62 9 h8 v2 h-8z" fill="#fff"/>
      <circle cx="94" cy="11" r="11" fill="var(--ink)"/>
      <rect x="88" y="7" width="12" height="8" fill="none" stroke="#fff" stroke-width="1.2"/>
      <path d="M88 7 l6 5 l6 -5" fill="none" stroke="#fff" stroke-width="1.2"/>
      <circle cx="122" cy="11" r="11" fill="var(--ink)"/>
      <circle cx="122" cy="11" r="5.5" fill="none" stroke="#fff" stroke-width="1.2"/>
      <path d="M116.5 11 h11 M122 5.5 q-3 5.5 0 11 q3 -5.5 0 -11" fill="none" stroke="#fff" stroke-width="1"/>
    </svg>
    <div class="contact">
      <div>555.014.2290</div>
      <div>info@brqnal.com</div>
      <div>www.brqnal-example.com</div>
      <div class="contact-rule"></div>
      <div>4120 Alder Park Drive</div>
      <div>Houston, TX 77019</div>
    </div>
  </section>

  <section class="card card-back">
    <div class="wordmark">BRQNAL</div>
    <div class="tagline">LAW ENFORCEMENT INNOVATION</div>
    <div class="divider"></div>
    <ul class="services">
      <li>LAW ENFORCEMENT</li>
      <li>JUSTICE OF THE PEACE</li>
      <li>MUNICIPAL COURTS</li>
    </ul>
  </section>
</body>
</html>
```